Brookvale Estates LLC stationary for a real estate property management company.

Create stationary (letterhead, envelopes, business cards) using Brookvale Estates LLC logo as primary creative element. Stationary design needs to be horizontal, leaving as much space as possible for correspondence copy. See attached Creative Brief and past stationary files for details.

Target Market(s)

Prospective apartment residents and current residents, vendors, and government agencies.

Industry/Entity Type

Property Management

Contact Information for Business Card

Business card employee title: Property Manager. Should include address, phone, fax, email, website, slogan, and Brookvale Estates logo.

Font styles to use
Sans Serif

Colors
0592cd
000000

Requirements
Must have
• Tone should be conservative, institutional, business (i.e. banking, finance, real estate). Must include: address, phone, fax, website, and slogan (see attached Creative Brief). Should be a horizontal design, leaving as much room as possible for letter correspondence copy.
Nice to have
• Please use an Arial or Helvetica style font.
Should not have
• Letterhead layout should leave as much room as possible for copy.

```html
<!DOCTYPE html>
<html lang="en">
<head>
<meta charset="UTF-8">
<title>Brookvale Estates LLC – Letterhead</title>
<link href="https://fonts.googleapis.com/css2?family=Open+Sans:wght@400;700&display=swap" rel="stylesheet">
<style>
  :root{
    --brand-blue:#0592cd;
    --ink:#000000;
    --text-grey:#6b6f75;
    --band-grey:#c9cbce;
    --paper:#ffffff;
    --backdrop:#dce9f7;
  }
  *{box-sizing:border-box;margin:0;padding:0}
  html,body{width:1200px;height:784px;overflow:hidden}
  body{background:var(--backdrop);font-family:"Open Sans",Arial,sans-serif;position:relative}
  .letterhead{
    position:absolute;left:60px;top:42px;width:1080px;height:700px;
    background:var(--paper);
    box-shadow:0 2px 14px rgba(30,80,150,.18);
  }
  .brand{
    position:absolute;top:58px;right:90px;
    display:flex;align-items:center;gap:12px;
  }
  .brand-square{width:30px;height:30px;background:var(--brand-blue)}
  .brand-text{display:flex;flex-direction:column}
  .brand-name{font-size:22px;font-weight:700;color:var(--brand-blue);letter-spacing:.5px;line-height:1.1}
  .brand-slogan{font-size:11px;color:var(--brand-blue);margin-top:3px}
  .edge-tab{position:absolute;height:5px;width:28px}
  .edge-tab.grey{background:var(--band-grey)}
  .edge-tab.blue{background:var(--brand-blue)}
  .tab-left-grey{left:0;top:40px}
  .tab-left-blue{left:0;top:48px;width:20px}
  .tab-right-grey{right:0;top:40px}
  .tab-right-blue{right:0;top:48px;width:20px}
  .footer-contact{
    position:absolute;left:40px;bottom:26px;
    display:flex;align-items:center;gap:10px;
    font-size:11.5px;color:var(--text-grey);
  }
  .contact-item{display:flex;align-items:center;gap:5px;white-space:nowrap}
  .contact-icon{width:12px;height:12px;flex:none}
  .footer-band{position:absolute;bottom:0;height:10px}
  .footer-band.blue{left:0;width:62%;background:var(--brand-blue)}
  .footer-band.grey{left:62%;right:0;background:linear-gradient(#e3e4e6,var(--band-grey))}
</style>
</head>
<body>
  <main class="letterhead">
    <div class="edge-tab grey tab-left-grey"></div>
    <div class="edge-tab blue tab-left-blue"></div>
    <div class="edge-tab grey tab-right-grey"></div>
    <div class="edge-tab blue tab-right-blue"></div>

    <header class="brand">
      <span class="brand-square"></span>
      <div class="brand-text">
        <span class="brand-name">BROOKVALE ESTATES LLC</span>
        <span class="brand-slogan">Multifamily Property Management</span>
      </div>
    </header>

    <footer class="footer-contact">
      <span class="contact-item">
        <svg class="contact-icon" viewBox="0 0 12 12"><circle cx="6" cy="6" r="6" fill="#0592cd"/><path d="M6 2.5a2.2 2.2 0 0 0-2.2 2.2C3.8 6.3 6 9.3 6 9.3s2.2-3 2.2-4.6A2.2 2.2 0 0 0 6 2.5z" fill="#fff"/></svg>
        2750 Alder Crest Drive #B210, Fairview, CA 92480
      </span>
      <span class="contact-item">
        <svg class="contact-icon" viewBox="0 0 12 12"><circle cx="6" cy="6" r="6" fill="#0592cd"/><path d="M4 3h1.3l.6 1.6-.8.6a4 4 0 0 0 1.7 1.7l.6-.8 1.6.6V8a1 1 0 0 1-1 1A5 5 0 0 1 3 4a1 1 0 0 1 1-1z" fill="#fff"/></svg>
        (000)-000-4817
      </span>
      <span class="contact-item">
        <svg class="contact-icon" viewBox="0 0 12 12"><circle cx="6" cy="6" r="6" fill="#0592cd"/><rect x="3" y="5" width="6" height="3.5" fill="#fff"/><rect x="4" y="3" width="4" height="2" fill="#fff"/></svg>
        (000)-000-4817
      </span>
      <span class="contact-item">
        <svg class="contact-icon" viewBox="0 0 12 12"><circle cx="6" cy="6" r="6" fill="#0592cd"/><circle cx="6" cy="6" r="3.3" fill="none" stroke="#fff" stroke-width=".9"/><path d="M2.7 6h6.6M6 2.7v6.6" stroke="#fff" stroke-width=".8"/></svg>
        www.brookvaleestates.us
      </span>
    </footer>

    <div class="footer-band blue"></div>
    <div class="footer-band grey"></div>
  </main>
</body>
</html>
```